R7M Horizon Business Card Design

We need a business card created for our New Business "R7M Horizon"<br/><br/>The business card design is up to you however the following information must be on the business card:<br/><br/>Front of the business card -<br/>Email :darrenp@r7mhorizon.nz<br/>Mobile: +64 (0) 22 4870 619<br/>Website: www.r7mhorizon.nz<br/>Card Owner Name: Darren Paltrow<br/>Company Title: Business Development Manager<br/>Slogan: "The PEAK of every view". <br/>Logo On the front attached to the design brief<br/><br/>On the back: <br/>Space on the back for 4 more versions of the logo across the bottom of the card indicating different subsidiary brands - R7M Coffee, R7M Arts, R7M ?? (The card will be used for all of these brands - We Will add the extra subsidiary logos to the design once the design is finished (We are a graphics design team). <br/><br/>Other than that we want a premium feeling logo that remains universally usable depending on the business entity that we are using the card for. The use of bright bold colours would be great but we still want the card to feel premium.
Target Market(s)
Gift Design and Manufacturing Companies
Contact Information for Business Card
Front of the business card -
Email :darrenp@r7mhorizon.nz
Mobile: +64 (0) 22 4870 619
Website: www.r7mhorizon.nz
Card Owner Name: Darren Paltrow
Company Title: Business Development Manager
Slogan: "The PEAK of every view".
Logo On the front attached to the design brief

```html
<!DOCTYPE html>
<html lang="en">
<head>
<meta charset="utf-8">
<title>R7M Horizon Business Card</title>
<link rel="stylesheet" href="https://fonts.googleapis.com/css2?family=Exo+2:wght@400;700;800&family=Open+Sans:wght@400;600;700&display=swap">
<style>
  :root {
    --bg: #4b4b4b;
    --ink-black: #111111;
    --panel-black: #1d1d1d;
    --brand-blue: #2f3f9e;
    --watermark: #eceef5;
    --text-grey: #333333;
    --white: #ffffff;
  }
  * { box-sizing: border-box; margin: 0; padding: 0; }
  html, body { width: 1200px; height: 900px; overflow: hidden; }
  body {
    background: var(--bg);
    font-family: "Open Sans", sans-serif;
    position: relative;
  }
  .card {
    position: absolute;
    left: 250px;
    width: 700px;
    height: 400px;
    border-radius: 28px;
    overflow: hidden;
  }
  .card--back { top: 35px; background: var(--ink-black); }
  .card--front { top: 465px; background: var(--white); }

  /* back */
  .back-name {
    position: absolute; left: 0; right: 0; top: 140px;
    text-align: center;
    font-family: "Exo 2", sans-serif;
    font-weight: 700;
    font-size: 54px;
    color: var(--white);
    letter-spacing: 1px;
  }
  .back-slogan {
    position: absolute; left: 0; right: 0; top: 300px;
    text-align: center; color: var(--white); font-size: 17px;
  }
  .back-slogan b { font-weight: 700; }
  .back-slogan .arrow { font-size: 11px; margin: 0 6px; }

  /* front */
  .front-shapes { position: absolute; inset: 0; }
  .watermark {
    position: absolute; left: 290px; top: 150px;
    font-family: "Exo 2", sans-serif; font-weight: 800;
    font-size: 62px; line-height: 1; color: var(--watermark); white-space: nowrap;
  }
  .holder { position: absolute; left: 62px; top: 62px; }
  .holder__name {
    font-family: "Exo 2", sans-serif; font-weight: 800;
    font-size: 30px; color: var(--brand-blue);
    text-transform: uppercase; letter-spacing: 1.5px;
  }
  .holder__title { font-size: 15px; color: var(--text-grey); margin-top: 2px; }
  .holder-rule {
    position: absolute; left: 62px; top: 140px; width: 580px;
    height: 1.5px; background: var(--brand-blue);
  }
  .contacts {
    position: absolute; left: 72px; top: 238px;
    list-style: none; font-size: 16px; color: var(--text-grey);
  }
  .contacts li { display: flex; align-items: center; gap: 10px; line-height: 25px; }
  .contacts svg { width: 13px; height: 13px; fill: var(--brand-blue); flex: none; }
  .panel-name {
    position: absolute; left: 566px; top: 266px;
    font-family: "Exo 2", sans-serif; font-weight: 700;
    font-size: 16px; color: var(--white); white-space: nowrap;
  }
  .panel-slogan {
    position: absolute; left: 546px; top: 354px;
    font-size: 12px; color: var(--white); white-space: nowrap;
  }
</style>
</head>
<body>

<section class="card card--back">
  <div class="back-name">R7M Horizon</div>
  <p class="back-slogan"><span class="arrow">◀</span>The <b>PEAK</b> of every view<span class="arrow">▶</span></p>
</section>

<section class="card card--front">
  <div class="watermark">R7M Horizon</div>
  <svg class="front-shapes" viewBox="0 0 700 400" width="700" height="400">
    <polygon points="558,248 700,222 700,318 542,322" fill="var(--brand-blue)"/>
    <polygon points="539,330 700,326 700,400 520,400" fill="var(--panel-black)"/>
    <polygon points="0,388 522,332 530,332 508,400 0,400" fill="var(--brand-blue)"/>
  </svg>

  <div class="holder">
    <h1 class="holder__name">Darren Paltrow</h1>
    <p class="holder__title">Business Development Manager</p>
  </div>
  <div class="holder-rule"></div>

  <ul class="contacts">
    <li>
      <svg viewBox="0 0 16 16"><path d="M3.6 1.2 6 4c.3.4.3.9 0 1.3L4.9 6.5a9 9 0 0 0 4.6 4.6l1.2-1.1c.4-.3.9-.3 1.3 0l2.8 2.4c.4.3.4.9 0 1.3l-1.3 1.2c-.7.6-1.7.8-2.6.4A15 15 0 0 1 1 5.2c-.4-.9-.2-1.9.4-2.6L2.6 1.3c.3-.4.7-.4 1-.1z"/></svg>
      +64 (0) 22 4870 619
    </li>
    <li>
      <svg viewBox="0 0 16 16"><path d="M1 3h14v10H1zm1.5 1.5v.3L8 8.6l5.5-3.8v-.3zm0 2.1v4.9h11V6.6L8 10.4z"/></svg>
      darrenp@r7mhorizon.nz
    </li>
    <li>
      <svg viewBox="0 0 16 16"><path d="M8 1a7 7 0 1 0 0 14A7 7 0 0 0 8 1zm0 1.5c.8 0 1.7 1.4 2 3.7H6c.3-2.3 1.2-3.7 2-3.7zM5.9 7.5h4.2a11 11 0 0 1 0 1H5.9a11 11 0 0 1 0-1zM2.6 7.5h2a12 12 0 0 0 0 1h-2a5.5 5.5 0 0 1 0-1zm8.8 0h2a5.5 5.5 0 0 1 0 1h-2a12 12 0 0 0 0-1zM6 9.8h4c-.3 2.3-1.2 3.7-2 3.7s-1.7-1.4-2-3.7z"/></svg>
      www.r7mhorizon.nz
    </li>
  </ul>

  <div class="panel-name">R7M Horizon</div>
  <p class="panel-slogan">The <b>PEAK</b> of every view</p>
</section>

</body>
</html>
```